ORLA - Óptica Médica - web design and concept

Website concept - Create and develop our website design and structure. ORLA is an optical store chain, and we are looking to establish our web and digital concept. In attachment there are several pictures about our stores and our logo.

The website structure should be user friendly. Colors should be light and the design as simple and minimalist as possible. There are different variations of the logothat can be used, check the file.

The website will include optical collections and sun collections as an online store. Also, a medical menu should be considered in order for clients to schedule optometry appointments. There should also be a menu for client assistance where the clients can read about glass maintenance in our workshop.
Updates

Low design quality

Number of Pages Required

5+ page

Font styles to use
Serif
Sans Serif

Requirements
Must have
• Must be user-friendly and minimalist.
• Please USE PICTURES FROM THE BRANDS we sell: MERUN, BOSKA, PNW, KOLE, BAMPE
Nice to have
• Nice to inspire: ZEK glasses (see website https://ch.shopzek.com/en/)
• Nice to inspire: https://merun-eyewear.com/
• Nice to ispire: https://www.pnwglobe.com/en/
Should not have
• Hysteric colors and shapes

```html
<!DOCTYPE html>
<html lang="en">
<head>
<meta charset="utf-8">
<title>ORLA – Óptica Médica</title>
<link rel="stylesheet" href="https://fonts.googleapis.com/css2?family=Open+Sans:wght@400;600;700&family=Roboto+Slab:wght@400;700&display=swap">
<style>
:root{
  --ink:#2b2f33;
  --muted:#6f7780;
  --blue:#1a9dc0;
  --teal:#62cdc6;
  --mist:#e9ecef;
  --mist-dark:#dde1e5;
  --line:#dfe3e6;
  --white:#ffffff;
}
*{box-sizing:border-box;margin:0;padding:0}
html,body{width:926px;height:1200px;overflow:hidden;background:var(--white)}
body{position:relative;font-family:"Open Sans",sans-serif;color:var(--ink)}
.abs{position:absolute}
.slab{font-family:"Roboto Slab",serif}

/* header */
.topbar{left:0;top:0;width:926px;height:42px;background:var(--mist)}
.tagline{left:212px;top:25px;font-size:7.5px;font-weight:600;color:var(--muted)}
.address{left:589px;top:25px;font-size:7.5px;color:var(--muted);display:flex;align-items:center;gap:4px}
.address b{color:var(--muted);font-weight:600}
.navband{left:0;top:42px;width:926px;height:62px;background:var(--white)}
.logo-plate{left:0;top:29px;width:206px;height:62px;background:var(--white);border-radius:0 14px 0 0}
.logo-disc{left:132px;top:38px;width:80px;height:80px;border-radius:50%;background:var(--white)}
.brand{left:142px;top:68px;width:60px;text-align:center;font-family:"Roboto Slab",serif;font-size:17px;letter-spacing:3px;color:var(--ink)}
.nav{left:450px;top:68px;display:flex;gap:0;font-family:"Roboto Slab",serif;font-size:9px;font-weight:700}
.nav a{position:absolute;white-space:nowrap;color:var(--ink);text-decoration:none}
.nav a.active{color:var(--blue)}
.nav a .plus{color:var(--blue)}
.nav-mark{left:493px;top:42px;width:84px;height:4px;background:var(--blue)}
.title-band{left:0;top:104px;width:926px;height:94px;background:linear-gradient(#e6e9ec,#fbfbfc);border-bottom:1px solid var(--line)}
.page-title{left:0;top:130px;width:964px;text-align:center;font-family:"Open Sans",sans-serif;font-size:20px;font-weight:600;color:#68717a;letter-spacing:.3px}

/* sidebar */
.sidemenu{left:157px;top:254px;width:141px;background:var(--white);box-shadow:0 0 3px rgba(0,0,0,.12)}
.sidemenu li{list-style:none;height:33.6px;line-height:33.6px;padding-left:14px;font-family:"Roboto Slab",serif;font-size:8.6px;color:var(--ink);border-bottom:1px solid #eef0f2}
.sidemenu li.current{background:var(--mist)}
.hours{left:157px;top:475px;width:141px;height:92px;background:var(--blue);color:var(--white);font-family:"Roboto Slab",serif;font-size:8.6px;padding:10px 14px}
.hours div{display:flex;justify-content:space-between;height:21px}
.photo-frame{left:0;top:577px;width:324px;height:325px;background:linear-gradient(135deg,#f3f3f3,#e2e2e2 60%,#eeeeee)}

/* content */
h2.section{font-family:"Roboto Slab",serif;font-weight:400;font-size:18px;color:#40464c}
.copy{font-size:9.4px;line-height:13.8px;color:var(--muted)}
.sub{font-family:"Roboto Slab",serif;font-size:10px;color:var(--ink)}
.link{font-size:9.4px;font-weight:600;color:var(--blue)}
.pic{background:linear-gradient(135deg,#e8ecef,#c9d3da 55%,#edf0f2)}

.price-col{width:203px}
.price-row{position:absolute;left:0;width:203px}
.price-row .name{font-size:10.2px;font-weight:600;color:var(--blue)}
.price-row .cost{position:absolute;right:0;top:0;font-size:10.2px;font-weight:600;color:var(--blue)}
.price-row .note{font-size:8.8px;line-height:13.6px;color:var(--muted);margin-top:2px}
.rule{position:absolute;left:0;width:203px;height:1px;background:var(--line)}
.pill{display:inline-block;margin-left:4px;padding:1px 6px;border:1px solid var(--blue);border-radius:9px;font-size:6px;font-weight:600;vertical-align:2px}

.promo{left:339px;top:781px;width:422px;height:121px;background:var(--mist);text-align:center}
.promo h3{margin-top:27px;font-family:"Roboto Slab",serif;font-weight:400;font-size:14.4px;color:#3f454b}
.btn{display:inline-block;background:var(--teal);color:var(--white);font-family:"Roboto Slab",serif;font-size:7.8px;text-align:center}
.promo .btn{margin-top:10px;width:112px;height:33px;line-height:33px}

/* footer */
.footer{left:0;top:957px;width:926px;height:209px;background:var(--mist)}
.footer-brand{left:196px;top:998px;width:80px;text-align:center;font-family:"Roboto Slab",serif;font-size:18px;letter-spacing:3px;color:var(--ink)}
.footer-text{left:157px;top:1034px;width:195px;font-size:9px;line-height:13.8px;color:var(--muted)}
.footer .btn{position:absolute}
.footer-btn{left:157px;top:1090px;width:90px;height:32px;line-height:32px}
.fcol h4{font-family:"Roboto Slab",serif;font-size:10px;color:var(--blue);font-weight:700;margin-bottom:12px}
.fcol li{list-style:none;font-family:"Roboto Slab",serif;font-size:7.6px;color:#40464c;height:20px}
.contact{left:576px;top:987px;width:194px;height:149px;background:var(--teal);color:var(--white);font-family:"Roboto Slab",serif}
.contact .label{position:absolute;left:54px;top:24px;font-size:7.6px;opacity:.85}
.contact .phone{position:absolute;left:54px;top:35px;font-size:10px;font-weight:700}
.contact .divider{position:absolute;left:25px;top:59px;width:144px;height:1px;background:rgba(255,255,255,.45)}
.contact .row{position:absolute;left:25px;display:flex;align-items:center;gap:6px;font-size:7.6px;font-weight:700}
.bottombar{left:0;top:1166px;width:926px;height:34px;background:var(--mist-dark)}
.social{left:732px;top:1177px;display:flex;gap:7px}
.social span{width:8px;height:8px;border-radius:50%;background:#7d858d}
</style>
</head>
<body>

<header>
  <div class="abs topbar"></div>
  <p class="abs tagline">An apple a day keeps the doctor away</p>
  <p class="abs address">
    <svg width="9" height="8" viewBox="0 0 10 9"><path d="M5 0 L10 4.5 H8.5 V9 H6 V6 H4 V9 H1.5 V4.5 H0 Z" fill="#8a929a"/></svg>
    Address: <b>48 Harlow Lane, Fenwick, SC 29410</b>
  </p>
  <div class="abs navband"></div>
  <div class="abs logo-plate"></div>
  <div class="abs logo-disc"></div>
  <div class="abs brand">ORLA</div>
  <div class="abs nav-mark"></div>
  <nav class="abs nav">
    <a style="left:0">Home <span class="plus">+</span></a>
    <a class="active" style="left:54px">Departments +</a>
    <a style="left:138px">Our Doctors <span class="plus">+</span></a>
    <a style="left:217px">News</a>
    <a style="left:263px">Contact Us</a>
  </nav>
  <div class="abs title-band"></div>
  <h1 class="abs page-title">Óptica Médica</h1>
</header>

<aside>
  <ul class="abs sidemenu">
    <li>Surgery and Radiology</li>
    <li>Family Medicine</li>
    <li>Women’s Health</li>
    <li class="current">Optician</li>
    <li>Pediatrics</li>
    <li style="border-bottom:0">Dermatology</li>
  </ul>
  <div class="abs hours">
    <div><span>Mon - Fri</span><span>0:00 - 24:00</span></div>
    <div><span>Sat - Sun</span><span>0:00 - 24:00</span></div>
    <div><span>Visit time</span><span>10:00 - 16:00</span></div>
    <div><span>All holidays</span><span>Open</span></div>
  </div>
  <div class="abs photo-frame" role="img" aria-label="Close-up of tortoiseshell eyeglasses resting on a pencil lens measurement sketch"></div>
</aside>

<main>
  <h2 class="abs section" style="left:331px;top:252px">Sight Checking</h2>
  <p class="abs copy" style="left:331px;top:279px;width:208px">World over people use massage therapy to help promote healthy skin, nourish and strengthen the body, relieve stress, reduce pain, and encourage balance and well being. Massage opens and increases the flow of energy, balancing the entire nervous system and helping to release physical.</p>
  <div class="abs pic" style="left:558px;top:256px;width:212px;height:106px" role="img" aria-label="Optician showing eyeglass frames to a customer in front of a display wall"></div>

  <h3 class="abs sub" style="left:331px;top:398px">Our Laboratory</h3>
  <p class="abs copy" style="left:331px;top:415px;width:208px">World over people use massage therapy to help promote healthy skin, nourish and strengthen the body, relieve stress, reduce pain.</p>
  <p class="abs link" style="left:331px;top:467px">How often should I have my eyes tested?</p>
  <p class="abs link" style="left:331px;top:491px">How old does my child have to be before test?</p>
  <div class="abs pic" style="left:558px;top:402px;width:212px;height:106px" role="img" aria-label="Optometrist examining a patient with a slit lamp beside an eye chart"></div>

  <h2 class="abs section" style="left:331px;top:541px">Pricing Table</h2>

  <section class="abs price-col" style="left:331px;top:585px">
    <div class="price-row" style="top:0"><div class="name">Simple Medical Form</div><div class="cost">Free</div><div class="note">Glasses can be quite pricy, even excluding the cost of frames.</div></div>
    <div class="rule" style="top:55px"></div>
    <div class="price-row" style="top:69px"><div class="name">Digital Retinal Photograph</div><div class="cost">$70</div></div>
    <div class="rule" style="top:96px"></div>
    <div class="price-row" style="top:110px"><div class="name">Simple Aviation Form</div><div class="cost">$105</div></div>
    <div class="rule" style="top:137px"></div>
    <div class="price-row" style="top:150px"><div class="name">Emergency Appointment</div><div class="cost">Free</div></div>
  </section>

  <section class="abs price-col" style="left:567px;top:585px">
    <div class="price-row" style="top:0"><div class="name">Cost of contacts<span class="pill">Get 10% Off</span></div><div class="cost">$30</div><div class="note">Glasses can be quite pricy, even excluding the cost of frames.</div></div>
    <div class="rule" style="top:57px"></div>
    <div class="price-row" style="top:71px"><div class="name">Additional Services</div><div class="cost">$33</div></div>
    <div class="rule" style="top:98px"></div>
    <div class="price-row" style="top:112px"><div class="name">Low Vision Aid Assessment</div><div class="cost">$23</div></div>
    <div class="rule" style="top:138px"></div>
    <div class="price-row" style="top:152px"><div class="name">DVLA Acuity Test</div><div class="cost">$20</div></div>
  </section>

  <div class="abs promo">
    <h3>Get 10% Off on All Prescription Glasses</h3>
    <a class="btn">Make an Appointment</a>
  </div>
</main>

<footer>
  <div class="abs footer">
    <a class="btn footer-btn">Buy Clarena</a>
  </div>
  <div class="abs footer-brand">ORLA</div>
  <p class="abs footer-text">Taking care of a sick child can be a frightening experience, we are extremely proud to have immediate assistance and advice.</p>

  <div class="abs fcol" style="left:366px;top:987px">
    <h4>Departments</h4>
    <ul><li>Surgery and Radiology</li><li>Family Medicine</li><li>Women’s Health</li><li>Optician</li><li>Pediatrics</li><li>Dermatology</li></ul>
  </div>
  <div class="abs fcol" style="left:471px;top:987px">
    <h4>Menu</h4>
    <ul><li>Departments</li><li>Our Doctors</li><li>News</li><li>Shop</li><li>Contact Us</li><li>Book an Appointment</li></ul>
  </div>

  <div class="abs contact">
    <svg style="position:absolute;left:25px;top:24px" width="20" height="20" viewBox="0 0 24 24"><path d="M6.6 10.8c1.4 2.8 3.8 5.1 6.6 6.6l2.2-2.2c.3-.3.7-.4 1-.2 1.1.4 2.3.6 3.6.6.6 0 1 .4 1 1V20c0 .6-.4 1-1 1C10.6 21 3 13.4 3 4c0-.6.4-1 1-1h3.5c.6 0 1 .4 1 1 0 1.3.2 2.5.6 3.6.1.3 0 .7-.2 1z" fill="#ffffff"/></svg>
    <span class="label">Emergency number</span>
    <span class="phone">803-555-0172</span>
    <div class="divider"></div>
    <div class="row" style="top:71px"><svg width="9" height="7" viewBox="0 0 10 8"><rect x=".5" y=".5" width="9" height="7" fill="none" stroke="#fff"/><path d="M.5 .5 L5 4.5 L9.5 .5" fill="none" stroke="#fff"/></svg>hello@orlaoptica.com</div>
    <div class="row" style="top:93px"><svg width="9" height="7" viewBox="0 0 10 8"><rect x=".5" y=".5" width="9" height="7" fill="none" stroke="#fff"/><path d="M.5 .5 L5 4.5 L9.5 .5" fill="none" stroke="#fff"/></svg>care@orlaoptica.com</div>
    <div class="row" style="top:115px"><svg width="9" height="8" viewBox="0 0 10 9"><path d="M5 0 L10 4.5 H8.5 V9 H6 V6 H4 V9 H1.5 V4.5 H0 Z" fill="#fff"/></svg>48 Harlow Lane, Fenwick</div>
  </div>

  <div class="abs bottombar"></div>
  <div class="abs social" aria-label="Social links"><span></span><span></span><span></span></div>
</footer>

</body>
</html>
```